Goodlooking website for a company who is working in the IT consultancy

We want a new website designed in WordPress. You can take www.kestrava.nl as an example. It should be a website with some short blocks of information about the company, nice pictures of our partners and our employees. A job page with a clear filter.

Target Market(s)

B2B

Industry/Entity Type

It Company

Coding

Coded - Design and coding required

Number of Pages Required

5+ page

Font styles to use
Sans Serif

Colors
0455a3
34a7d8

Requirements
Must have
• Check briefing

```html
<!DOCTYPE html>
<html lang="en">
<head>
<meta charset="utf-8">
<title>Kestrava – Critical IT Solutions</title>
<link href="https://fonts.googleapis.com/css2?family=Montserrat:wght@300;400;600;700&family=Work+Sans:wght@400;500;600&display=swap" rel="stylesheet">
<style>
:root{
  --teal:#15b2a6;
  --teal-dark:#0fa38f;
  --sky:#29a9d6;
  --ink:#333b44;
  --text:#5c6470;
  --card-title:#555c64;
  --pale:#eef4f9;
  --black:#000;
  --white:#fff;
  --line:#dfe3e8;
}
*{box-sizing:border-box;margin:0;padding:0}
html,body{width:1200px;height:2791px;overflow:hidden;background:var(--white)}
body{font-family:"Work Sans",sans-serif;color:var(--text);position:relative}
a{color:inherit;text-decoration:none}
.brand{display:flex;align-items:center;gap:12px;font-family:"Work Sans",sans-serif;font-weight:600;color:var(--ink)}
.brand-dot{width:60px;height:60px;border-radius:50%;background:var(--teal)}
/* header */
.site-header{height:110px;display:flex;align-items:center;justify-content:space-between;padding:0 87px}
.site-header .brand{font-size:32px;letter-spacing:2px}
.main-nav{display:flex;gap:44px;font-size:14px;color:var(--ink);font-weight:400}
/* hero */
.hero{position:relative;height:508px;background:linear-gradient(180deg,#2d2a3a 0%,#3b3a4c 45%,#4a4b55 100%);color:var(--white)}
.hero-photo{position:absolute;inset:0;background:linear-gradient(90deg,rgba(40,38,52,.9),rgba(60,62,80,.55) 60%,rgba(35,36,48,.85))}
.hero-copy{position:absolute;left:86px;top:146px;font-family:"Montserrat",sans-serif}
.hero-kicker{font-size:26px;font-weight:300}
.hero-title{font-size:51px;font-weight:700;line-height:64px;margin-top:2px}
.btn-outline{display:inline-block;margin-top:26px;border:2px solid var(--white);padding:9px 26px;font-size:18px}
.hero-arrow{position:absolute;top:240px;width:26px;height:26px;display:flex;align-items:center;justify-content:center}
.hero-arrow.prev{left:28px;background:var(--teal)}
.hero-arrow.next{right:28px}
/* about */
.about{height:478px;text-align:center;padding-top:64px}
.section-title{font-size:44px;font-weight:500;color:var(--ink)}
.section-title span{color:var(--sky)}
.about p{width:830px;margin:26px auto 0;font-size:14.5px;line-height:23px}
.btn-pill{display:inline-block;margin-top:36px;background:var(--teal);color:var(--white);border-radius:26px;padding:15px 34px;font-size:14px}
/* solutions */
.solutions{position:relative;height:600px;background:linear-gradient(180deg,#1a2633,#2a3440 50%,#3a3a30);text-align:center;padding-top:74px}
.solutions .section-title{color:var(--white)}
.cards{display:flex;gap:11px;justify-content:center;margin-top:40px}
.card{width:247px;height:350px;background:var(--white);border-radius:3px;overflow:hidden}
.card-img{height:168px}
.card h3{font-size:15px;font-weight:600;color:var(--card-title);margin:18px 0 10px}
.card p{font-size:12.5px;line-height:19px;padding:0 10px;height:76px;overflow:hidden}
.card a{display:block;margin-top:22px;font-size:12.5px}
/* vacancies & contact */
.jobs-contact{height:414px;display:flex;padding:0 86px}
.vacancies{width:536px;padding-top:54px}
.vacancies h2{font-size:32px;font-weight:500;color:var(--teal-dark)}
.job{height:50px;border:1px solid var(--line);display:flex;align-items:center;padding:0 14px 0 20px;margin-top:13px}
.job:first-of-type{margin-top:20px}
.job h3{flex:1;font-size:17px;font-weight:500;color:var(--ink)}
.btn-sm{font-size:12px;font-weight:600;color:var(--white);padding:7px 14px;border-radius:2px;margin-left:8px}
.btn-dark{background:#3a4450}.btn-teal{background:var(--teal)}
.quick-contact{width:464px;margin-left:28px;background:var(--teal-dark);padding:40px 41px}
.quick-contact h2{text-align:center;color:var(--white);font-size:30px;font-weight:500;margin-bottom:26px}
.field{background:var(--white);height:44px;margin-bottom:5px;border-radius:2px;padding:12px 16px;font-size:11px;color:#999}
.field.msg{height:66px}
.btn-send{display:inline-block;margin-top:6px;background:#0b2521;color:var(--white);font-size:12px;padding:8px 40px}
/* partners */
.partners{height:323px;background:var(--pale);text-align:center;padding-top:84px}
.partner-row{display:flex;justify-content:center;align-items:center;gap:60px;margin-top:40px}
.partner-badge{height:44px;border-radius:4px;background:#b9c6d4}
/* footer */
.site-footer{height:358px;background:var(--black);color:#ccc;position:relative;padding:0 87px}
.footer-brand{position:absolute;left:87px;top:100px}
.footer-brand .brand{color:var(--white);font-size:32px;letter-spacing:2px}
.footer-brand .brand-dot{width:80px;height:80px}
.footer-col{position:absolute;top:42px}
.footer-col h4{font-family:"Montserrat",sans-serif;font-weight:400;font-size:18px;color:#eee;margin-bottom:26px}
.contact-list li{list-style:none;display:flex;gap:24px;font-size:13px;margin-bottom:13px;line-height:22px}
.contact-list svg{flex:none;margin-top:5px}
.links li{list-style:none;font-size:13px;margin-bottom:6px}
.links li::before{content:">";margin-right:14px}
.nl-input{width:213px;height:40px;border:1px solid #aaa;padding:12px 18px;font-size:11px;margin-bottom:10px}
.nl-btn{width:213px;height:36px;background:var(--teal);border:1px solid var(--white);color:var(--white);font-weight:600;font-size:15px;text-align:center;line-height:34px}
.footer-rule{position:absolute;left:87px;right:87px;top:263px;border-top:1px solid #333}
.copyright{position:absolute;left:87px;top:294px;font-size:13px}
.social{position:absolute;right:87px;top:286px;display:flex;gap:10px}
.social span{width:32px;height:32px;border-radius:50%;background:#555}
</style>
</head>
<body>
<header class="site-header">
  <div class="brand"><span class="brand-dot"></span>KESTRAVA</div>
  <nav class="main-nav"><a>Home</a><a>Solutions</a><a>Our Team</a><a>Partners</a><a>Vacancies</a><a>Contact</a></nav>
</header>

<section class="hero">
  <div class="hero-photo" role="img" aria-label="City skyline with office towers at dusk"></div>
  <div class="hero-copy">
    <div class="hero-kicker">We Build</div>
    <h1 class="hero-title">Mission Critical<br>Environments.</h1>
    <a class="btn-outline">Get Started</a>
  </div>
  <span class="hero-arrow prev"><svg width="10" height="12"><path d="M7 1L2 6l5 5" stroke="#fff" stroke-width="2" fill="none"/></svg></span>
  <span class="hero-arrow next"><svg width="10" height="12"><path d="M3 1l5 5-5 5" stroke="#fff" stroke-width="2" fill="none"/></svg></span>
</section>

<section class="about">
  <h2 class="section-title">About <span>Kestrava</span></h2>
  <p>Sed ut perspiciatis unde omnis iste natus error sit voluptatem accusantium doloremque laudantium, totam rem aperiam, eaque ipsa quae ab illo inventore veritatis et quasi architecto beatae vitae dicta sunt explicabo. Nemo enim ipsam voluptatem quia voluptas sit aspernatur aut odit aut fugit, sed quia consequuntur magni dolores eos qui ratione voluptatem sequi nesciunt. Neque porro quisquam est, qui dolorem ipsum quia dolor sit amet, consectetur, adipisci velit, sed quia non numquam eius modi tempora incidunt ut labore et dolore magnam aliquam quaerat voluptatem. Ut enim ad minima veniam, quis nostrum exercitationem ullam corporis suscipit laboriosam, nisi ut aliquid ex ea commodi consequatur? Quis autem vel eum iure reprehenderit qui in ea voluptate velit esse quam nihil molestiae consequatur, vel illum qui dolorem eum fugiat quo voluptas nulla pariatur?</p>
  <a class="btn-pill">Read More Kestrava</a>
</section>

<section class="solutions" role="region" aria-label="Solutions over a night city backdrop">
  <h2 class="section-title">Our <span>Solutions</span></h2>
  <div class="cards">
    <article class="card">
      <div class="card-img" role="img" aria-label="Hand touching an automation interface" style="background:linear-gradient(135deg,#2d4f78,#6f92b8)"></div>
      <h3>Automation &amp; Deployment</h3>
      <p>Kestrava provides services that ensure that your "automation" is automated. Within IT environments repetitive tasks often take place that</p>
      <a>Learn More</a>
    </article>
    <article class="card">
      <div class="card-img" role="img" aria-label="Businessman with cloud security symbols" style="background:linear-gradient(135deg,#3f9ad8,#cfe6f6)"></div>
      <h3>Mission Critical Solutions</h3>
      <p>Kestrava is the specialist in the construction and management of Mission Critical Systems. Our Mission Critical team can design IT environments</p>
      <a>Learn More</a>
    </article>
    <article class="card">
      <div class="card-img" role="img" aria-label="Laptop showing cloud service screen" style="background:linear-gradient(135deg,#3a3d42,#b9bcc0)"></div>
      <h3>Cloud Consultancy</h3>
      <p>Cloud services are nowadays an indispensable part of the IT landscape. Where previously an application was installed on a physical computer</p>
      <a>Learn More</a>
    </article>
    <article class="card">
      <div class="card-img" role="img" aria-label="Chalkboard sketch of hybrid cloud types" style="background:linear-gradient(135deg,#1b1b1b,#3a3a3a)"></div>
      <h3>Hyperconverged Infrastructures</h3>
      <p>Among other things, Kestrava supplies Nodara products in which computing power, storage and networks are fully integrated and in which</p>
      <a>Learn More</a>
    </article>
  </div>
</section>

<section class="jobs-contact">
  <div class="vacancies">
    <h2>Vacancies</h2>
    <div class="job"><h3>Systems Engineer</h3><a class="btn-sm btn-dark">View More</a><a class="btn-sm btn-teal">Apply Now</a></div>
    <div class="job"><h3>Network Engineer</h3><a class="btn-sm btn-dark">View More</a><a class="btn-sm btn-teal">Apply Now</a></div>
    <div class="job"><h3>Finibus Bonorum</h3><a class="btn-sm btn-dark">View More</a><a class="btn-sm btn-teal">Apply Now</a></div>
    <div class="job"><h3>The standard Lorem</h3><a class="btn-sm btn-dark">View More</a><a class="btn-sm btn-teal">Apply Now</a></div>
  </div>
  <div class="quick-contact">
    <h2>Quick Contact</h2>
    <div class="field">Name</div>
    <div class="field">Phone</div>
    <div class="field">Email</div>
    <div class="field msg">Message</div>
    <a class="btn-send">SEND</a>
  </div>
</section>

<section class="partners">
  <h2 class="section-title">Our <span>Partners</span></h2>
  <div class="partner-row">
    <span class="partner-badge" style="width:100px"></span>
    <span class="partner-badge" style="width:100px"></span>
    <span class="partner-badge" style="width:152px"></span>
    <span class="partner-badge" style="width:200px"></span>
  </div>
</section>

<footer class="site-footer">
  <div class="footer-brand"><div class="brand"><span class="brand-dot"></span>KESTRAVA</div></div>
  <div class="footer-col" style="left:426px">
    <h4>Contact Info:</h4>
    <ul class="contact-list">
      <li><svg width="10" height="13"><path d="M5 0a5 5 0 0 1 5 5c0 3-5 8-5 8S0 8 0 5a5 5 0 0 1 5-5z" fill="#ccc"/><circle cx="5" cy="5" r="2" fill="#000"/></svg><span>Lindenhof 14,<br>3512 KM Veldhaven</span></li>
      <li><svg width="12" height="12"><path d="M2 0l3 3-1.5 2a8 8 0 0 0 3.5 3.5L9 7l3 3-2 2C5 12 0 7 0 2z" fill="#ccc"/></svg><span>Tel: 010-5550142</span></li>
      <li><svg width="13" height="10"><rect width="13" height="10" fill="#ccc"/><path d="M0 0l6.5 5L13 0" stroke="#000" fill="none"/></svg><span>Mail: info@kestrava.nl</span></li>
    </ul>
  </div>
  <div class="footer-col" style="left:684px">
    <h4>Quick Links:</h4>
    <ul class="links"><li>Home</li><li>Solutions</li><li>Our Team</li><li>Partners</li><li>Vacancies</li><li>Contact</li></ul>
  </div>
  <div class="footer-col" style="left:899px">
    <h4>Newsletter Signup</h4>
    <div class="nl-input">Email Address</div>
    <div class="nl-btn">SUBMIT</div>
  </div>
  <div class="footer-rule"></div>
  <p class="copyright">Copyright © 2018. Kestrava Critical IT Solutions . All rights reserved.</p>
  <div class="social"><span></span><span></span><span></span><span></span><span></span></div>
</footer>
</body>
</html>
```